BFCM Creatives Theme

We are looking for an initial design for our BFCM campaign this year to set the theme for all other creatives for BFCM. We are an ecommerce brand selling Merino wool baby clothing. Our flagship product is the Marlow Toddler Hush Pod (see images).

We are starting with the request for an instagram post, announcing the sale (details below). This post should be 1080x1350 but also look appealing in the square grid. I've attached a basic brand card showing color palette, fonts, and logos. I will also attach some image options. We are looking for your creativity to shine while aligning with our branding and connecting with the customer. If you have a specific idea and are looking for a specific image please contact us.

Sale Details:
- 20% Off Sitewide
- 11.28.24 - 12.02.24
- Excluding giftcards and imperfects. No rainchecks.

```html
<!DOCTYPE html>
<html lang="en">
<head>
<meta charset="utf-8">
<title>Fleecewell BFCM Sale Post</title>
<link rel="stylesheet" href="https://fonts.googleapis.com/css2?family=Poppins:wght@500;600;800&family=Kalam:wght@300&display=swap">
<style>
  :root {
    --stage: #e9e9e9;
    --slate: #7a8390;
    --sage: #c5d2c3;
    --cream: #efefed;
    --ink: #333436;
    --white: #ffffff;
    --photo-light: #ecebe8;
    --photo-blue: #6f95c4;
    --photo-tan: #dcc9a0;
  }
  * { margin: 0; padding: 0; box-sizing: border-box; }
  html, body {
    width: 1200px;
    height: 1197px;
    overflow: hidden;
    background: var(--stage);
  }
  .post {
    position: absolute;
    left: 121px;
    top: 0;
    width: 1080px;
    height: 1350px;
    transform: scale(0.8867);
    transform-origin: 0 0;
    overflow: hidden;
    background: var(--slate);
    font-family: "Poppins", sans-serif;
  }
  .post-shapes { position: absolute; inset: 0; }
  .brand-tag {
    position: absolute;
    left: 0; top: 64px;
    width: 457px; height: 105px;
    background: var(--white);
    display: flex;
    align-items: center;
    gap: 18px;
    padding-left: 34px;
  }
  .brand-dot {
    width: 62px; height: 62px;
    border-radius: 50%;
    background: var(--ink);
  }
  .brand-name {
    font-weight: 500;
    font-size: 60px;
    color: var(--ink);
    letter-spacing: -1px;
  }
  .offer {
    position: absolute;
    left: 54px; top: 848px;
    color: var(--ink);
    font-weight: 800;
    line-height: 1;
  }
  .offer-amount { font-size: 218px; letter-spacing: -4px; line-height: 190px; }
  .offer-word { font-size: 218px; letter-spacing: -4px; line-height: 190px; }
  .offer-scope { font-size: 100px; font-weight: 800; line-height: 110px; margin-top: 6px; }
  .sale-dates {
    position: absolute;
    left: 659px; top: 959px;
    width: 421px; height: 56px;
    background: var(--cream);
    border-radius: 28px 0 0 28px;
    color: var(--ink);
    font-weight: 600;
    font-size: 40px;
    line-height: 56px;
    padding-left: 34px;
    letter-spacing: -0.5px;
  }
  .calendar-icon {
    position: absolute;
    left: 845px; top: 876px;
    width: 68px; height: 70px;
  }
  .sale-terms {
    position: absolute;
    left: 712px; top: 1066px;
    list-style: none;
    font-family: "Kalam", cursive;
    font-weight: 300;
    font-size: 39px;
    line-height: 54px;
    color: var(--cream);
  }
  .sale-terms li { position: relative; padding-left: 44px; }
  .sale-terms li::before {
    content: "";
    position: absolute;
    left: 10px; top: 22px;
    width: 14px; height: 14px;
    border-radius: 50%;
    background: var(--cream);
  }
</style>
</head>
<body>
  <main class="post">
    <svg class="post-shapes" width="1080" height="1350" viewBox="0 0 1080 1350">
      <defs>
        <clipPath id="hero-clip"><circle cx="660" cy="220" r="530"/></clipPath>
        <linearGradient id="hero-fill" x1="0" y1="0" x2="0" y2="1">
          <stop offset="0" stop-color="var(--photo-light)"/>
          <stop offset="0.45" stop-color="#e3dccb"/>
          <stop offset="0.75" stop-color="var(--photo-blue)"/>
          <stop offset="1" stop-color="#7fa2cc"/>
        </linearGradient>
      </defs>
      <circle class="hero-ring" cx="690" cy="275" r="545" fill="var(--sage)"/>
      <g clip-path="url(#hero-clip)">
        <rect class="hero-photo" role="img" aria-label="Photo of a smiling baby lying on a white sheet wearing a blue hot-air-balloon print sleep sack" x="0" y="0" width="1080" height="760" fill="url(#hero-fill)"/>
      </g>
      <circle class="offer-ring" cx="303" cy="1172" r="394" fill="var(--sage)"/>
      <circle class="offer-disc" cx="273" cy="1162" r="385" fill="var(--cream)"/>
    </svg>

    <div class="brand-tag">
      <span class="brand-dot"></span>
      <span class="brand-name">Fleecewell</span>
    </div>

    <div class="offer">
      <div class="offer-amount">20%</div>
      <div class="offer-word">OFF</div>
      <div class="offer-scope">Sitewide</div>
    </div>

    <svg class="calendar-icon" viewBox="0 0 68 70" aria-hidden="true">
      <rect x="2" y="8" width="64" height="60" rx="7" fill="var(--ink)"/>
      <rect x="7" y="22" width="54" height="41" rx="2" fill="var(--slate)"/>
      <rect x="15" y="1" width="7" height="15" rx="3.5" fill="var(--ink)" stroke="var(--slate)" stroke-width="2"/>
      <rect x="46" y="1" width="7" height="15" rx="3.5" fill="var(--ink)" stroke="var(--slate)" stroke-width="2"/>
      <g fill="var(--ink)">
        <rect x="11" y="26" width="9" height="8"/><rect x="23" y="26" width="9" height="8"/><rect x="35" y="26" width="9" height="8"/><rect x="47" y="26" width="9" height="8"/>
        <rect x="11" y="38" width="9" height="8"/><rect x="23" y="38" width="9" height="8"/><rect x="35" y="38" width="9" height="8"/><rect x="47" y="38" width="9" height="8"/>
        <rect x="11" y="50" width="9" height="8"/><rect x="23" y="50" width="9" height="8"/><rect x="35" y="50" width="9" height="8"/>
      </g>
    </svg>

    <div class="sale-dates">11.28.24 - 12.02.24</div>

    <ul class="sale-terms">
      <li>Excluding giftcards<br>and imperfects</li>
      <li>No rainchecks</li>
    </ul>
  </main>
</body>
</html>
```